Business Card Design & Gift cards, Gift Cert, Donation Card

Retail Gift Store-in addition to Business Cards we'd like sequenced 2 sided Gift cards, Gift Certificate Cards, and Donation Cards.please see examples and email for clarificationlogos attached with examples-
Gift Card, Gift Certificate and Donation Card will all be same style just differant upper right title, with back side info as example.
business card, as example is single sided.
looking for additional ideas for layout

Industry/Entity Type

Business

Contact Information for Business Card

211 Newman St.East Tawas, MI 48730989.362.8730Office@BrewKrew.com

Requirements
Must have
• Blue as per example
• Logos provided
• like gradiant background

```html
<!DOCTYPE html>
<html lang="en">
<head>
<meta charset="utf-8">
<title>Tillow Marsh – Gift Card &amp; Business Card</title>
<link rel="stylesheet" href="https://fonts.googleapis.com/css2?family=Comic+Neue:wght@400;700&display=swap">
<style>
  :root {
    --page-bg: #e9e6e1;
    --card-white: #ffffff;
    --card-fade: #d4d4d4;
    --band-black: #0a0a0a;
    --lower-gray-top: #6e6e6e;
    --lower-gray-bottom: #3c3c3c;
    --ink: #1a1a1a;
    --rule: #8a8a8a;
    --text-light: #f4f4f4;
    --brand-blue: #1f2fb5;
    --brand-sun: #f2c21b;
  }
  * { box-sizing: border-box; margin: 0; padding: 0; }
  html, body { width: 1200px; height: 843px; overflow: hidden; }
  body {
    background: var(--page-bg);
    font-family: "Comic Neue", "Comic Sans MS", cursive;
    color: var(--ink);
    position: relative;
  }
  .card {
    position: absolute;
    width: 560px;
    height: 320px;
    border-radius: 22px;
    overflow: hidden;
    box-shadow: 0 10px 28px rgba(0,0,0,.22);
  }

  /* Gift card back */
  .gift-card {
    left: 40px; top: 110px;
    background: linear-gradient(160deg, var(--card-white) 45%, var(--card-fade) 100%);
  }
  .card-number {
    position: absolute; right: 34px; top: 22px;
    font-size: 15px;
  }
  .card-number-rule {
    position: absolute; right: 34px; top: 48px; width: 360px;
    border-top: 1px solid var(--rule);
  }
  .field {
    position: absolute; left: 34px;
    display: flex; align-items: flex-end; gap: 10px;
    font-weight: 700;
  }
  .field .label { white-space: nowrap; }
  .field .line { border-bottom: 1px solid var(--rule); flex: 1; height: 1px; margin-bottom: 5px; }
  .field-to   { top: 78px;  width: 490px; font-size: 21px; }
  .field-from { top: 122px; width: 490px; font-size: 21px; }
  .field-issued  { top: 188px; width: 360px; font-size: 17px; }
  .field-expires { top: 222px; width: 360px; font-size: 17px; }
  .field-employee{ top: 256px; width: 360px; font-size: 17px; }

  .brand-mark {
    position: absolute; right: 28px; top: 178px;
    display: flex; align-items: center; gap: 8px;
    color: var(--brand-blue);
    font-weight: 700; font-size: 18px;
  }
  .brand-mark .dot {
    width: 18px; height: 18px; border-radius: 50%;
    background: var(--brand-sun);
  }

  /* Business card front */
  .business-card {
    left: 600px; top: 420px;
    background: linear-gradient(180deg, var(--card-white) 0%, #f1f1f1 100%);
  }
  .business-name {
    position: absolute; left: 0; right: 0; top: 34px;
    text-align: center;
    font-size: 50px; font-weight: 400; letter-spacing: 2px;
    color: var(--ink);
  }
  .offer-band {
    position: absolute; left: 0; right: 0; top: 132px; height: 72px;
    background: var(--band-black);
    color: var(--text-light);
    text-align: center;
    font-size: 17px; line-height: 24px;
    padding-top: 12px;
  }
  .contact-panel {
    position: absolute; left: 0; right: 0; top: 204px; bottom: 0;
    background: linear-gradient(180deg, var(--lower-gray-top), var(--lower-gray-bottom));
    color: var(--text-light);
    font-size: 17px; line-height: 25px;
    padding: 14px 0 0 40px;
  }
  .contact-panel b { font-weight: 700; }
</style>
</head>
<body>

  <section class="card gift-card" aria-label="Gift card back">
    <p class="card-number">Card Number : 58724</p>
    <div class="card-number-rule"></div>

    <div class="field field-to"><span class="label">To :</span><span class="line"></span></div>
    <div class="field field-from"><span class="label">Form :</span><span class="line"></span></div>
    <div class="field field-issued"><span class="label">Date Issued :</span><span class="line"></span></div>
    <div class="field field-expires"><span class="label">Expiration Date :</span><span class="line"></span></div>
    <div class="field field-employee"><span class="label">Employee :</span><span class="line"></span></div>

    <div class="brand-mark"><span class="dot"></span>Tillow Marsh</div>
  </section>

  <section class="card business-card" aria-label="Business card front">
    <h1 class="business-name">TILLOW MARSH</h1>
    <div class="offer-band">
      <p>Gourmet Food | Fine Wines | Gift Baskets</p>
      <p>Kitchen &amp; Bath Accessories | Candles | Cards | Soaps</p>
    </div>
    <div class="contact-panel">
      <p>482 Larkfield Ave. Pine Harbor, MI 48731</p>
      <p><b>P:</b> 989.517.4296 &nbsp;<b>E:</b> Office@TillowMarsh.com</p>
      <p><b>W:</b> www.TillowMarsh.com</p>
    </div>
  </section>

</body>
</html>
```